In need of a Wordpress website for a Water Sports Rental Company!

We are starting a new venture that provides a variety of rental equipment in the Cayman Islands. We are in need of a website where guests are able to book their rental gear during their stay in Cayman. We will also have an interactive map where guests can learn about off the beaten path activities to explore in here Cayman.

Our target market is middle/upper class, so we need a website that appeals to this group. We need our website to be clean, simple and easy to navigate. We need it to be highly visual and modern. We like the idea of the website having a tropical feel to it, we are very open to creative ideas that reflects this!

Must be designed in WordPress using the Velmora template I’ve provided.

You will find all instructions & the photos I want to use for this website on the following stashvo account:
- www.stashvo.com
- Username: hello@lumentrips.com
- Password: pelican7

All of the photos will need to be resized accordingly to be as small as possible without loosing resolution.

These are the tabs that will be used:
- Home Page
- Adventure Map
- Rental Gear
- Tours
- Photo Gallery
- Contact Us

Home Page
- You will find all the text and instructions for the home page in the word document named ‘Home Page’.

Adventure Map
- You will find all the text and instructions for the home page in the word document named ‘Adventure Map Content’
- There will also be a few 'guide' pages under this tab, which we will go in to detail with the winner.

Rentals
- You will find all the text and instructions for the Rentals page in the word document named ‘Rentals Content’

Tours
- This will just be a page saying ‘kayaking, snorkeling & Bioluminescence tours coming soon’.

Photo Gallery
- You will find the photos for this in our Stashvo.com Account

Contact Us
- Send us a Message – page will be similar to our other site http://lumentrips.com/contact/
- Phone: +1 (345) 555 0192
- Email: hello@tidalotterco.com

The big factors on who will have the winning design are:
- The background used
- The layout of the Home Page
- The animations at the top of the Rental Landing Page
- The overall clean, professional look to the website

If you have any questions, don't hesitate to ask.

We look forward to working with you all!!

Good luck!!

Target Market(s)

Middle/Upper Class on vacation with their family

Industry/Entity Type

It Company

Coding

Coded - Design and coding required

Number of Pages Required

5+ page

Colors
fffbf0
cadf82
fbf289
f6faec
fdf9cf
eaf2ce
fff3d1
fee18a
abd037

Requirements
Must have
• - Must be designed in Wordpress using the Velmora template I have provided or another suitable web template.
• - Must be Responsive Web Design so that the website adjusts to various screen sizes.

```html
<!DOCTYPE html>
<html lang="en">
<head>
<meta charset="utf-8">
<title>Tidal Otter Co. — Water Sports Rental</title>
<link rel="stylesheet" href="https://fonts.googleapis.com/css2?family=Oswald:wght@300;400&family=Open+Sans:wght@400;600&display=swap">
<style>
:root{
  --green:#abd037;
  --green-light:#cadf82;
  --yellow:#fee18a;
  --yellow-soft:#fde79a;
  --cream:#fffbf0;
  --wood:#e8eaec;
  --ink:#2b2b2b;
  --text:#555;
  --footer:#f3f3f1;
  --white:#fff;
}
*{margin:0;padding:0;box-sizing:border-box}
html,body{width:1200px;height:4260px;overflow:hidden}
body{background:linear-gradient(90deg,#e3e5e8,#eef0f2 30%,#e6e8eb 60%,#eff1f3);font-family:"Open Sans",sans-serif;color:var(--text);position:relative}
.topbar{height:30px;background:var(--yellow);font-size:11px;color:#555;display:flex;justify-content:flex-end;align-items:center;gap:44px;padding-right:158px}
.topbar span{display:flex;align-items:center;gap:7px}
.brand{position:absolute;top:62px;left:0;width:1200px;text-align:center}
.brand-mark{display:inline-flex;align-items:center;gap:12px;margin-top:40px}
.brand-dot{width:34px;height:34px;border-radius:50%;background:var(--green)}
.brand-name{font-family:"Oswald",sans-serif;font-size:34px;color:#1f4d5c;font-weight:400}
.tagline{font-family:"Oswald",sans-serif;font-size:15px;color:#222;margin-top:38px;font-weight:300}
.page{position:absolute;left:132px;top:255px;width:936px}
.nav{height:47px;background:var(--green);display:flex;align-items:center;position:relative}
.nav a{font-family:"Oswald",sans-serif;color:#fff;font-size:15px;text-decoration:none;padding:0 21px;font-weight:300;height:47px;line-height:47px}
.nav a.active{border-bottom:2px solid #fff}
.nav .search{position:absolute;right:0;top:0;width:80px;height:47px;background:var(--yellow);clip-path:polygon(22% 0,100% 0,100% 100%,0 100%);display:flex;align-items:center;justify-content:flex-end;padding-right:16px}
.hero{height:476px;background:linear-gradient(180deg,#2f7f8f 0%,#3c8d88 45%,#5a8a55 80%,#3e6a4a 100%);position:relative;text-align:center;color:#fff}
.hero .play{position:absolute;left:438px;top:165px}
.hero h1{position:absolute;top:240px;width:100%;font-family:"Oswald",sans-serif;font-weight:400;font-size:42px;letter-spacing:.5px}
.hero p{position:absolute;top:303px;width:100%;font-family:"Oswald",sans-serif;font-weight:300;font-size:14px}
.arrow{position:absolute;top:203px;width:36px;height:40px;background:#1b1b1b;display:flex;align-items:center;justify-content:center}
.arrow.l{left:0}.arrow.r{right:0}
.content{background:var(--white);padding-top:40px}
.features{display:flex;gap:28px;padding:0 25px;height:331px;border-bottom:1px solid #eee}
.feature{width:276px;text-align:center}
.feature .pic{height:182px;border-radius:14px 14px 50% 50%/14px 14px 26px 26px;border-bottom:3px solid #e2e2e2}
.feature h3{font-family:"Oswald",sans-serif;font-weight:300;font-size:20px;color:#333;margin-top:14px}
.feature p{font-size:10px;line-height:19px;margin-top:10px;padding:0 14px}
.welcome{text-align:center;padding:52px 40px 0}
.welcome h2{font-family:"Oswald",sans-serif;font-weight:300;font-size:31px;color:#222}
.welcome p{font-size:10px;line-height:19px;margin-top:14px}
.rows{margin:52px 25px 0}
.row{display:flex;height:294px}
.row .pic{width:443px;height:294px}
.row .txt{width:443px;padding:0 28px;display:flex;flex-direction:column;justify-content:center}
.row h3{font-family:"Oswald",sans-serif;font-weight:300;font-size:19px;color:#222;line-height:30px;text-transform:uppercase}
.row p{font-size:10px;line-height:19px;margin-top:14px}
.btn{display:inline-block;width:92px;height:26px;line-height:26px;border-radius:13px;background:var(--green);color:#fff;font-family:"Oswald",sans-serif;font-size:12px;text-align:center;margin-top:20px}
.picks{background:var(--yellow);margin-top:72px;height:402px;padding-top:40px;text-align:center}
.picks h2{font-family:"Oswald",sans-serif;font-weight:300;font-size:32px;color:#222}
.picks-grid{display:flex;gap:13px;padding:0 25px;margin-top:30px}
.pick{width:212px;background:#fff}
.pick .pic{height:178px}
.pick span{display:block;height:45px;line-height:45px;font-family:"Oswald",sans-serif;font-weight:300;font-size:17px;color:#222}
.footer{background:var(--footer);height:292px;display:flex;padding:38px 23px 0}
.footer h4{font-family:"Oswald",sans-serif;font-weight:300;font-size:19px;color:#222;text-transform:uppercase}
.quote{width:440px}
.quote p{font-size:10px;line-height:17px;margin-top:18px}
.form{display:grid;grid-template-columns:211px 211px;gap:12px 13px;margin-top:14px}
.form div{height:39px;border:1px solid #d5d5d5;background:#fff;font-size:10px;padding:13px 12px}
.form .submit{background:var(--green);color:#fff;text-align:center;border:none;font-size:11px;font-weight:600}
.contact{width:272px;margin-left:74px;padding-top:10px}
.contact p{font-size:11px;line-height:18px;margin-top:16px}
.contact .line{display:flex;gap:14px;margin-top:16px;font-size:11px;line-height:18px}
.links{padding-top:6px}
.links ul{list-style:none;margin-top:14px}
.links li{font-size:10px;line-height:20.5px}
.links li::before{content:"›";margin-right:9px;color:#333}
.copy{height:70px;background:#fff;text-align:center;line-height:70px;font-size:10px;color:#444}
</style>
</head>
<body>
<div class="topbar">
  <span><svg width="11" height="11" viewBox="0 0 24 24"><path fill="#444" d="M6.6 10.8a15 15 0 006.6 6.6l2.2-2.2c.3-.3.7-.4 1-.2 1.1.4 2.3.6 3.6.6.6 0 1 .4 1 1V20c0 .6-.4 1-1 1A17 17 0 013 4c0-.6.4-1 1-1h3.5c.6 0 1 .4 1 1 0 1.3.2 2.5.6 3.6.1.3 0 .7-.2 1z"/></svg>Phone: 0431 555 208</span>
  <span><svg width="12" height="10" viewBox="0 0 24 18"><rect x="1" y="1" width="22" height="16" fill="none" stroke="#444" stroke-width="2"/><path d="M1 1l11 9 11-9" fill="none" stroke="#444" stroke-width="2"/></svg>Email: info@tidalotterco.com</span>
</div>

<header class="brand">
  <div class="brand-mark"><span class="brand-dot"></span><span class="brand-name">Tidal Otter Co.</span></div>
  <div class="tagline">Cayman's Premier Adventure and Rental Company</div>
</header>

<main class="page">
  <nav class="nav">
    <a class="active">Home</a><a>Adventure Map</a><a>Rental Gear</a><a>Tours</a><a>Photo Gallery</a><a>Contact Us</a>
    <div class="search"><svg width="20" height="20" viewBox="0 0 24 24"><circle cx="10" cy="10" r="7" fill="none" stroke="#333" stroke-width="2"/><path d="M15 15l6 6" stroke="#333" stroke-width="2.5"/></svg></div>
  </nav>

  <section class="hero" role="img" aria-label="Snorkeler swimming above sea grass in clear water">
    <svg class="play" width="60" height="60" viewBox="0 0 60 60"><circle cx="30" cy="30" r="27" fill="none" stroke="#fff" stroke-width="3"/><path d="M24 18l18 12-18 12z" fill="#fff"/></svg>
    <h1>WATER SPORTS RENTAL</h1>
    <p>Cayman's Premier Adventure and Rental Company</p>
    <div class="arrow l"><svg width="12" height="16" viewBox="0 0 12 16"><path d="M9 2L3 8l6 6" fill="none" stroke="#fff" stroke-width="2.5"/></svg></div>
    <div class="arrow r"><svg width="12" height="16" viewBox="0 0 12 16"><path d="M3 2l6 6-6 6" fill="none" stroke="#fff" stroke-width="2.5"/></svg></div>
  </section>

  <div class="content">
    <section class="features">
      <article class="feature">
        <div class="pic" role="img" aria-label="Two people paddling a blue kayak in turquoise water" style="background:linear-gradient(180deg,#9fcbe6 0%,#6fb7a8 30%,#2fb1b8 60%,#34a8b0 100%)"></div>
        <h3>Exploration</h3>
        <p>Rent everything you need to get outside and explore the island on your own terms. Snorkel the Kittiwake, check out</p>
      </article>
      <article class="feature">
        <div class="pic" role="img" aria-label="Person relaxing in an inflatable kayak near the shore" style="background:linear-gradient(180deg,#a8d0ea 0%,#7bb59a 32%,#3fbab8 60%,#2ea7a7 100%)"></div>
        <h3>Relaxation</h3>
        <p>We will come straight to your resort or condo and set everything up for you and your family to enjoy our kayaks and paddle boards</p>
      </article>
      <article class="feature">
        <div class="pic" role="img" aria-label="Placeholder image for education" style="background:#ececec"></div>
        <h3>Education</h3>
        <p>We love sharing our knowledge on Cayman's history and the island's extraordinary marine life. We'll also teach you everything you need</p>
      </article>
    </section>

    <section class="welcome">
      <h2>Welcome to Tidal Otter Co.!</h2>
      <p>We love having the freedom to explore when travelling and we bet you do too! We are Grand Cayman's premier rental company, offering everything you need to make the most of your vacation. Our website serves as a great starting point to help you prepare for your vacation here in Cayman. We feature a huge selection of adventures on our interactive map with tons of useful information, pictures and directions. Our adventure map is the perfect guide to all our great spots to check out here in Cayman.</p>
    </section>

    <section class="rows">
      <div class="row">
        <div class="pic" role="img" aria-label="Several kayaks paddling over shallow turquoise water" style="background:linear-gradient(180deg,#a9d2ec 0%,#5f9d7a 18%,#3cb6be 40%,#2a9aa6 100%)"></div>
        <div class="txt"><h3>Your one stop shop for all the rentals<br>you need here in Cayman!</h3>
        <p>We have a have a huge array of fun toys and equipment for you to enjoy. Whether it's for exploring or relaxing, we have all the equipment you need to make the most of your trip here in Cayman. Need something that we don't stock, just ask and we'll do everything we can to get you the gear you need!</p><span class="btn">Read More</span></div>
      </div>
      <div class="row">
        <div class="txt"><h3>Check out our interactive map<br>of Cayman!</h3>
        <p>You won't find any tourist traps on our map! We're all about getting off the beaten path and finding those unique spots and natural wonders to explore. Get our expert advice on which adventures are best for you and how to tackle them!</p><span class="btn">Read More</span></div>
        <div class="pic" role="img" aria-label="Illustrated adventure map of Grand Cayman" style="background:linear-gradient(135deg,#5fc6e0 0%,#7fd0e4 45%,#f2e6a4 70%,#6fc4de 100%)"></div>
      </div>
      <div class="row">
        <div class="pic" role="img" aria-label="Two people in a clear-water kayak under a bright sky" style="background:linear-gradient(180deg,#3f8ed2 0%,#9ccbee 40%,#bfe6ea 62%,#8fd3cf 100%)"></div>
        <div class="txt"><h3>Enjoy complete freedom to explore.</h3>
        <p>Inflatable kayaks have revolutionized the way kayak exploration is done in a way never before. Our kayaks give you the freedom to explore Cayman's most secluded locations and snorkel those hard to reach reefs. Our kayaks are light, comfortable and easy to use.</p><span class="btn">Read More</span></div>
      </div>
      <div class="row">
        <div class="txt"><h3>There's no easier way to get around the island.</h3>
        <p>What better way is there to explore the island other than to rent a bike and go? Our mountain bikes are perfect for those interested on heading out on a full day adventure. If you're looking for something more casual, renting a cruiser is perfect to get around the Seven Mile Beach area. Use our map to help guide you to all our suggested locations to explore!</p><span class="btn">Read More</span></div>
        <div class="pic" role="img" aria-label="Two beach cruiser bikes parked on white sand" style="background:linear-gradient(180deg,#6fb6dc 0%,#a8d6ea 40%,#ece7dc 60%,#e2dbcf 100%)"></div>
      </div>
      <div class="row">
        <div class="pic" role="img" aria-label="Placeholder image for concierge service" style="background:#e9e9e9"></div>
        <div class="txt"><h3>We want to be your personal concierge and<br>help you to plan out your trip!</h3>
        <p>When we come to deliver your equipment, we teach you everything you need to know about the island including the best hidden spots, best restaurants &amp; bars to eat &amp; drink and anything else you might be curious about. Please don't hesitate to contact us for any and all of your vacation questions.</p><span class="btn">Read More</span></div>
      </div>
      <div class="row">
        <div class="txt"><h3>Is it a boat? Is it a whale?.... It's a Floatnest!</h3>
        <p>Easily one of the coolest inventions we've ever come across, the Floatnest is a versatile toy the whole family can enjoy together. Spend the day cruising along Seven Mile Beach in style as you bar hop with your clan. Better still, bring a cooler on board and put the kids to work paddling as you relax in your hammock on the crystal clear waters!</p><span class="btn">Read More</span></div>
        <div class="pic" role="img" aria-label="Floating hammock raft on turquoise water" style="background:linear-gradient(180deg,#4fb9bf 0%,#3aa9b1 50%,#2b94a0 100%)"></div>
      </div>
      <div class="row">
        <div class="pic" role="img" aria-label="Two snorkelers underwater with full face masks and a sea scooter" style="background:linear-gradient(180deg,#5ab3d6 0%,#3d8fc2 40%,#7fb5cf 75%,#c9d8d6 100%)"></div>
        <div class="txt"><h3>A new way to snorkel!</h3>
        <p>Our full face snorkel masks are easy to use, making them perfect for kids and beginners. You simply put the mask on and breath as you usually would. There's no need to get used to breathing from your mouth and you don't expe­rience a sore jaw from having to hold the mouth piece in place. Just ask and we'll bring one along for you to try!</p><span class="btn">Read More</span></div>
      </div>
    </section>

    <section class="picks">
      <h2>Our Adventure Top-Picks</h2>
      <div class="picks-grid">
        <div class="pick"><div class="pic" role="img" aria-label="Glowing blue bioluminescent bay at night" style="background:linear-gradient(180deg,#05081a 0%,#0b1d4a 55%,#1f5fc8 100%)"></div><span>Bio Bay</span></div>
        <div class="pick"><div class="pic" role="img" aria-label="Sunken shipwreck underwater" style="background:linear-gradient(180deg,#2e7f9e 0%,#4a7f86 55%,#6b6a5c 100%)"></div><span>Kittiwake</span></div>
        <div class="pick"><div class="pic" role="img" aria-label="Aerial view of a small sand cay in the sea" style="background:linear-gradient(180deg,#2a6fa1 0%,#3d8cb5 45%,#c9d7c6 62%,#3d93b6 100%)"></div><span>Sand Cay Island</span></div>
        <div class="pick"><div class="pic" role="img" aria-label="Stingrays swimming in shallow clear water" style="background:linear-gradient(180deg,#5fb8c0 0%,#4aa9b1 50%,#6fbfb8 100%)"></div><span>Stingray City</span></div>
      </div>
    </section>

    <footer class="footer">
      <div class="quote">
        <h4>Get a Quote</h4>
        <p>Lorem ipsum dolor sit amet, consectetur adipiscing elit, sed do eiusmod tempor incidi­dunt ut labore et dolore magna aliqua. Ut enim ad minim veniam,</p>
        <div class="form"><div>Name</div><div>E - Mail</div><div>Phone No</div><div class="submit">SUBMIT</div></div>
      </div>
      <div class="contact">
        <h4>Contact Us</h4>
        <p>Tidal Otter Co.<br>218 Harbour Lane, Suite 4<br>George Town, KY1 1102</p>
        <div class="line"><svg width="16" height="16" viewBox="0 0 24 24"><path fill="#abd037" d="M6.6 10.8a15 15 0 006.6 6.6l2.2-2.2c.3-.3.7-.4 1-.2 1.1.4 2.3.6 3.6.6.6 0 1 .4 1 1V20c0 .6-.4 1-1 1A17 17 0 013 4c0-.6.4-1 1-1h3.5c.6 0 1 .4 1 1 0 1.3.2 2.5.6 3.6.1.3 0 .7-.2 1z"/></svg><span>Phone: 1-800-555-0147<br>345-555-0163</span></div>
        <div class="line"><svg width="16" height="13" viewBox="0 0 24 18"><rect x="1" y="1" width="22" height="16" fill="none" stroke="#abd037" stroke-width="2"/><path d="M1 1l11 9 11-9" fill="none" stroke="#abd037" stroke-width="2"/></svg><span>info@tidalotterco.com</span></div>
      </div>
      <div class="links">
        <h4>Quick Links</h4>
        <ul><li>Home</li><li>Adventure Map</li><li>Rental Gear</li><li>Tours</li><li>Photo Gallery</li><li>Contact Us</li></ul>
      </div>
    </footer>
    <div class="copy">2017 © Copyrights Tidal Otter Co. All Rights Reserved</div>
  </div>
</main>
</body>
</html>
```